Hello my Name is Elias Moreno. I buy and sell vintage comic books, you can refer to my instragram page qpkz.comics to get ideas and inspiration. For the front of the card I would like my company logo QPKZ Comics with a yellow and black background with the bat signal or bat emblem like on my IG page and with my info Elias Moreno as the Owner and address/ phone number, PO Box 617283, Miami, FL 33827, 305-482-6170 and that I buy and sell comics & collectables . Also feel free to be open to other ideas if you want. Im not stuck on one design. For the back of the card I would like for it to say follow me on Instagram QPKZ.Comics with the ig emblem. Also would like the card to be vertical if possible. Thanks

```html
<!DOCTYPE html>
<html lang="en">
<head>
<meta charset="utf-8">
<title>QPKZ Comics – Business Cards</title>
<link rel="stylesheet" href="https://fonts.googleapis.com/css2?family=Open+Sans:wght@400;600;700;800&display=swap">
<style>
  :root {
    --page-bg: #ececec;
    --card-white: #f7f7f7;
    --brand-yellow: #f6c519;
    --text-grey: #555555;
    --pure-white: #ffffff;
    --card-shadow: rgba(0, 0, 0, 0.14);
  }
  * { box-sizing: border-box; margin: 0; padding: 0; }
  html, body {
    width: 1200px;
    height: 900px;
    overflow: hidden;
    background: var(--page-bg);
    font-family: "Open Sans", Arial, sans-serif;
  }
  .canvas {
    position: relative;
    width: 1200px;
    height: 900px;
    display: flex;
    align-items: center;
    justify-content: center;
    gap: 50px;
  }
  .card {
    position: relative;
    width: 520px;
    height: 297px;
    overflow: hidden;
    box-shadow: 0 6px 18px var(--card-shadow);
  }

  /* Front: contact side */
  .card--contact { background: var(--card-white); }
  .contact-name {
    position: absolute;
    left: 36px; top: 30px;
    color: var(--brand-yellow);
    font-weight: 700;
    font-size: 20px;
    letter-spacing: 0.5px;
    text-transform: uppercase;
  }
  .contact-role {
    position: absolute;
    left: 36px; top: 56px;
    color: var(--text-grey);
    font-size: 13px;
  }
  .contact-list {
    position: absolute;
    left: 36px; top: 94px;
    list-style: none;
    color: var(--text-grey);
    font-size: 14px;
    line-height: 19px;
  }
  .contact-list li { display: flex; align-items: flex-start; gap: 8px; }
  .contact-list svg { flex: none; margin-top: 3px; }
  .tagline-band {
    position: absolute;
    left: 0; right: 0;
    top: 178px; height: 54px;
    background: var(--brand-yellow);
    display: flex;
    align-items: center;
    padding-left: 36px;
  }
  .tagline {
    color: var(--pure-white);
    font-weight: 700;
    font-size: 12.5px;
    letter-spacing: 0.2px;
    white-space: nowrap;
    text-transform: uppercase;
  }
  .brand-mark {
    position: absolute;
    width: 150px; height: 150px;
    border-radius: 50%;
    display: flex;
    align-items: center;
    justify-content: center;
    text-align: center;
  }
  .brand-mark span {
    font-weight: 800;
    font-size: 24px;
    line-height: 1.05;
    text-transform: uppercase;
  }
  .card--contact .brand-mark {
    right: 18px; top: 112px;
    background: var(--brand-yellow);
  }
  .card--contact .brand-mark span { color: var(--pure-white); }

  /* Back: social side */
  .card--social { background: var(--brand-yellow); }
  .social-band {
    position: absolute;
    left: 0; right: 0;
    top: 208px; height: 56px;
    background: var(--pure-white);
    display: flex;
    align-items: center;
    justify-content: center;
    gap: 10px;
    color: var(--brand-yellow);
    font-weight: 600;
    font-size: 13px;
  }
  .social-label { text-transform: uppercase; letter-spacing: 0.4px; }
  .social-dot {
    width: 22px; height: 22px;
    border-radius: 50%;
    background: var(--brand-yellow);
  }
  .social-handle { font-weight: 700; }
  .card--social .brand-mark {
    left: 185px; top: 50px;
    background: var(--pure-white);
  }
  .card--social .brand-mark span { color: var(--brand-yellow); }
</style>
</head>
<body>
<main class="canvas">

  <section class="card card--contact" aria-label="Business card front">
    <h1 class="contact-name">Elias Moreno</h1>
    <p class="contact-role">Owner</p>
    <ul class="contact-list">
      <li>
        <svg width="11" height="13" viewBox="0 0 11 13" aria-hidden="true">
          <path d="M2.2 0.5 L4 3.2 L2.9 4.6 C3.6 6.4 4.8 7.7 6.5 8.7 L7.8 7.6 L10.5 9.4 L9.6 11.6 C5 11.2 0.9 7 0.4 1.6 Z" fill="var(--brand-yellow)"/>
        </svg>
        <span>305-482-6170</span>
      </li>
      <li>
        <svg width="11" height="14" viewBox="0 0 11 14" aria-hidden="true">
          <path d="M5.5 0.5 C2.7 0.5 0.6 2.6 0.6 5.3 C0.6 8.6 5.5 13.5 5.5 13.5 C5.5 13.5 10.4 8.6 10.4 5.3 C10.4 2.6 8.3 0.5 5.5 0.5 Z M5.5 7.2 A1.9 1.9 0 1 1 5.5 3.4 A1.9 1.9 0 1 1 5.5 7.2 Z" fill="var(--brand-yellow)"/>
        </svg>
        <span>PO Box 617283,<br>Miami, FL 33827</span>
      </li>
    </ul>
    <div class="tagline-band">
      <p class="tagline">We buy and sell comics &amp; collectables</p>
    </div>
    <div class="brand-mark"><span>QPKZ<br>Comics</span></div>
  </section>

  <section class="card card--social" aria-label="Business card back">
    <div class="social-band">
      <span class="social-label">Follow me on</span>
      <span class="social-dot" aria-hidden="true"></span>
      <span class="social-handle">QPKZ.Comics</span>
    </div>
    <div class="brand-mark"><span>QPKZ<br>Comics</span></div>
  </section>

</main>
</body>
</html>
```